New Service Brochure for The Brellford Spa

Hi All! We are looking for a new brochure design- tri-fold, double sided, and full color. We are a certified Tallow Spa for men and women in the heart of the Catskill Mountains of upstate New York. Our clients would describe us as laid back luxury with no pretensions and a home away from home vibe. Our font is Avalon. Key colors are black, white and gold. Looking for an inviting, clean, and modern/minimalist spread with a touch of elegance. No orchid imagery, please. I would like our "Tallow Spa" logo on cover, too please. Front cover image with with logo and "Tallow Spa" Sticker . Bottom of back with contact info. We would prefer massages go on left inside page, facials in middle and right inside, nails on back left, but we are open to new or different layout proposals. Thank you!

Target Market(s)

Men & Women.

Industry/Entity Type

Health And Wellness

Other font styles liked:
• Avalon is our signature font

Requirements
Must have
• Easy on the eyes.
Nice to have
• Negative space.
Should not have
• No orchids. Busy lines and wild colors.

```html
<!DOCTYPE html>
<html lang="en">
<head>
<meta charset="utf-8">
<title>The Brellford Spa – Brochure Final Files</title>
<link rel="stylesheet" href="https://fonts.googleapis.com/css2?family=Cormorant+Garamond:wght@400&family=PT+Sans:wght@400;700&display=swap">
<style>
  :root {
    --paper: #fdfbf8;
    --faded-text: #cfc8c0;
    --faded-title: #c3bab0;
    --faded-line: #e2dcd4;
    --logo-tone: #cdc4b8;
    --photo-warm-1: #f3ece4;
    --photo-warm-2: #e9dfd3;
    --photo-skin: #efe2d8;
    --badge: #dfe3d6;
    --web-bar: #d9d6d2;
    --band: rgba(40, 40, 40, 0.8);
    --band-text: #ffffff;
  }
  * { margin: 0; padding: 0; box-sizing: border-box; }
  html, body { width: 1200px; height: 932px; overflow: hidden; background: var(--paper); }
  .canvas {
    position: relative; width: 1200px; height: 932px; overflow: hidden;
    background: var(--paper);
    font-family: "PT Sans", Arial, sans-serif;
  }
  .abs { position: absolute; }

  /* Left panel: hands & feet menu */
  .section-tag {
    left: 108px; top: 56px; width: 182px; height: 37px;
    border: 1.5px solid var(--faded-line);
    color: var(--faded-text); font-size: 20px; letter-spacing: 1px;
    display: flex; align-items: center; justify-content: center;
  }
  .intro {
    left: 108px; top: 106px; width: 268px;
    color: var(--faded-text); font-size: 16px; line-height: 27px;
  }
  .menu-item { left: 21px; width: 354px; }
  .menu-item h3 {
    display: flex; justify-content: space-between;
    font-size: 11px; font-weight: 700; color: var(--faded-title);
    line-height: 13px;
  }
  .menu-item p { font-size: 9.5px; line-height: 13px; color: var(--faded-text); }
  .photo-hands {
    left: 0; top: 783px; width: 387px; height: 149px;
    background: linear-gradient(120deg, var(--photo-skin), var(--photo-warm-1) 60%, var(--photo-warm-2));
  }

  /* Middle panel */
  .photo-lounge {
    left: 387px; top: 0; width: 405px; height: 263px;
    background: linear-gradient(180deg, var(--photo-warm-2), var(--photo-warm-1) 55%, #f7f2ec);
  }
  .middle-copy {
    left: 387px; width: 405px; text-align: center;
    color: var(--faded-text); font-size: 15px; line-height: 24px;
  }
  .middle-name {
    left: 387px; top: 400px; width: 405px; text-align: center;
    font-family: "Cormorant Garamond", Georgia, serif;
    font-size: 50px; line-height: 50px; color: var(--logo-tone);
  }
  .contact {
    left: 387px; top: 800px; width: 405px; text-align: center;
    color: var(--faded-text); font-size: 14px; line-height: 19px;
  }
  .contact .gap { height: 12px; }

  /* Right panel: cover */
  .cover-frame {
    left: 802px; top: 15px; width: 376px; height: 258px;
    border: 1.5px solid var(--faded-line); border-bottom: none;
  }
  .cover-name {
    left: 802px; top: 40px; width: 376px; text-align: center;
    font-family: "Cormorant Garamond", Georgia, serif;
    font-size: 60px; line-height: 62px; color: var(--logo-tone);
  }
  .cover-tagline {
    left: 802px; top: 238px; width: 376px; text-align: center;
    color: var(--faded-text); font-size: 19px;
  }
  .photo-towels {
    left: 792px; top: 273px; width: 408px; height: 659px;
    background: linear-gradient(160deg, var(--photo-warm-1), var(--photo-warm-2) 60%, #e4d7ca);
  }
  .badge {
    left: 1095px; top: 757px; width: 90px; height: 90px;
    border-radius: 50%; background: var(--badge);
  }
  .web-bar {
    left: 847px; top: 880px; width: 293px; height: 34px;
    background: var(--web-bar);
    color: #f4f2ef; font-size: 15px;
    display: flex; align-items: center; justify-content: center;
  }

  /* Overlay band */
  .files-band {
    left: 0; top: 273px; width: 1200px; height: 510px;
    background: var(--band);
    border-top-right-radius: 60px;
  }
  .files-text {
    left: 0; top: 340px; width: 1230px; text-align: center;
    color: var(--band-text); font-weight: 700;
  }
  .files-title { font-size: 33px; line-height: 40px; margin-bottom: 66px; }
  .files-list { font-size: 35px; line-height: 50px; }
</style>
</head>
<body>
<div class="canvas">

  <!-- Left panel -->
  <div class="abs section-tag">HANDS &amp; FEET</div>
  <p class="abs intro">Please visit our website for our most current offerings of evolving and extraordinary nail care services. Below is a sampling of some of our favorite seasonal and standard manicures and pedicures.</p>

  <div class="abs menu-item" style="top:279px;"><h3><span>Garden Greens Manicure</span><span>$45</span></h3>
    <p>Hydrate, smooth and clarify tired hands with a blend of fresh greens, a crisp cleansing soak and a warm hand treatment finished with polish. 55 minutes.</p></div>
  <div class="abs menu-item" style="top:314px;"><h3><span>Warm Stone Manicure</span><span>$55</span></h3>
    <p>Dissolve tension and strain with the comfort of warm stones and a slow hand massage. Hands and arms are smoothed with a rich botanical balm and finished with heated herbal mitts and a fresh coat of polish. 55 minutes.</p></div>
  <div class="abs menu-item" style="top:370px;"><h3><span>Age Defying Hand Ritual</span><span>$75</span></h3>
    <p>A gentle scrub, brightening masque and firming cream work together to restore soft, youthful looking hands with lasting moisture. 55 minutes.</p></div>
  <div class="abs menu-item" style="top:418px;"><h3><span>Cedar Mint Pedicure</span><span>$65</span></h3>
    <p>A fragrant warm soak, cooling mint scrub and rich whipped lotion leave tired feet calm, smooth and renewed after a long day. 55 minutes.</p></div>
  <div class="abs menu-item" style="top:462px;"><h3><span>Herbal Root Pedicure</span><span>$65</span></h3>
    <p>Soothe and detoxify with a warm herbal root soak and gentle sea salt exfoliation. A calming mask of clay and fresh botanicals draws out impurities while a slow massage with warm oil eases tired muscles. Heels are softened, nails are shaped and cuticles are tended before a cooling wrap and a finishing layer of rich butter. Perfect for the change of seasons. 55 minutes.</p></div>
  <div class="abs menu-item" style="top:558px;"><h3><span>Soothing Botanical Manicure</span><span>$55</span></h3>
    <p>Provide real relief for overworked hands with soothing botanicals that ease stiffness and boost circulation. Includes a warm soak, exfoliation, hand and arm massage, cuticle and nail care and polish. 55 minutes.</p></div>
  <div class="abs menu-item" style="top:612px;"><h3><span>Citrus Forest Pedicure</span><span>$65</span></h3>
    <p>A perfect pick me up for any feet that want to celebrate the season. Citrus soak, pine salt scrub, warm oil massage, cuticle and nail care with a polish of your choice to finish. 55 minutes.</p></div>
  <div class="abs menu-item" style="top:672px;"><h3><span>Restorative Pedicure</span><span>$70</span></h3>
    <p>An anti-inflammatory soak and mineral salt scrub are followed by warm towels and a focused foot and calf massage with a cooling menthol lotion to ease pain and promote complete comfort. A must for runners, hikers and anyone on their feet all day. Cuticle care and polish included. 55 minutes.</p></div>

  <div class="abs photo-hands" role="img" aria-label="Photo of hands and feet receiving a manicure and pedicure"></div>

  <!-- Middle panel -->
  <div class="abs photo-lounge" role="img" aria-label="Photo of a guest relaxing in a bright spa lounge"></div>
  <p class="abs middle-copy" style="top:306px;">Visit our website 24/7 to print or email<br>gift certificates and to view our</p>
  <div class="abs middle-name">The<br>Brellford Spa</div>
  <p class="abs middle-copy" style="top:676px;">seasonal packages, feature services,<br>and spa policies.</p>
  <div class="abs contact">
    <p>(518) 555-0142</p>
    <p>Info@TheBrellfordSpa.com</p>
    <div class="gap"></div>
    <p>24 Alder Hollow Road</p>
    <p>Brellford, NY 12490</p>
    <p>Just off Main Street!</p>
  </div>

  <!-- Right panel -->
  <div class="abs cover-frame"></div>
  <div class="abs cover-name">The<br>Brellford Spa</div>
  <p class="abs cover-tagline">a boutique spa for Men &amp; Women</p>
  <div class="abs photo-towels" role="img" aria-label="Photo of rolled white spa towels"></div>
  <div class="abs badge"></div>
  <div class="abs web-bar">www.thebrellfordspa.com</div>

  <!-- Final files overlay -->
  <div class="abs files-band"></div>
  <div class="abs files-text">
    <p class="files-title">Final Revised Files:</p>
    <p class="files-list">Source File zipped folder contains .VDS<br>(Vectra Draw Studio) inside/outside of<br>brochure and font files<br>Print File zipped folder contains PDF<br>inside/outside of brochure</p>
  </div>

</div>
</body>
</html>
```